Fast Growing Personal Injury Law Firm Needs Business Card Design

We need a business card design for a fast growing personal injury law firm in Florida. Our name is Dorian Kalvenfeld, P.A. Our practice is comprised of younger attorneys (in their 30s) that employ more modern techniques/tools than our older competition. We would prefer a look that is a modern play on a classic look. Also, we would like to continue using a color scheme that employs navy blue and kelly green (other shades of green could be fine too) as well as our "E" logo.

Industry/Entity Type

Law Firm

```html
<!DOCTYPE html>
<html lang="en">
<head>
<meta charset="utf-8">
<title>Dorian Kalvenfeld, P.A. — Business Cards</title>
<link rel="stylesheet" href="https://fonts.googleapis.com/css2?family=Cinzel:wght@600&family=Crimson+Text:ital,wght@0,400;0,600;1,400&display=swap">
<style>
  :root {
    --navy-deep: #1b2f6e;
    --navy: #27489a;
    --navy-light: #3b64b8;
    --kelly: #0f9a4a;
    --kelly-deep: #087a38;
    --kelly-light: #19b25a;
    --gold: #f1e23a;
    --lime: #c9dc4a;
    --white: #ffffff;
    --backdrop: #e9e6df;
  }
  * { box-sizing: border-box; margin: 0; padding: 0; }
  html, body { width: 1200px; height: 900px; overflow: hidden; }
  body {
    background: var(--backdrop);
    font-family: "Crimson Text", Georgia, serif;
    color: var(--white);
  }
  .canvas {
    position: relative;
    width: 1200px;
    height: 900px;
  }
  .card {
    position: absolute;
    top: 302px;
    width: 520px;
    height: 297px;
    border-radius: 4px;
    overflow: hidden;
    box-shadow: 0 10px 24px rgba(0,0,0,0.22);
  }

  /* Front card */
  .card-front {
    left: 50px;
    background: radial-gradient(ellipse at 45% 55%, var(--navy-light) 0%, var(--navy) 45%, var(--navy-deep) 100%);
  }
  .card-front .mark {
    position: absolute; left: 28px; top: 26px;
    width: 62px; height: 62px;
    background: var(--kelly);
    border: 4px solid var(--white);
  }
  .card-front .firm {
    position: absolute; left: 104px; top: 30px;
  }
  .firm-name {
    font-family: "Cinzel", "Times New Roman", serif;
    font-weight: 600;
    font-size: 25px;
    letter-spacing: 1px;
    line-height: 1.1;
    color: var(--white);
  }
  .firm-tagline {
    font-family: "Crimson Text", Georgia, serif;
    font-size: 15.5px;
    letter-spacing: 1.2px;
    text-transform: uppercase;
    color: var(--gold);
    margin-top: 2px;
  }
  .card-front .person {
    position: absolute; left: 28px; top: 116px;
  }
  .person-name { font-size: 24px; line-height: 1.1; }
  .person-title { font-size: 17px; color: var(--lime); margin-top: 4px; }
  .divider {
    position: absolute; left: 222px; top: 112px;
    width: 1px; height: 66px;
    background: var(--white);
    transform: rotate(12deg);
  }
  .contact {
    position: absolute; left: 246px; top: 110px;
    list-style: none; font-size: 16px; line-height: 1.3;
  }
  .address {
    position: absolute; left: 28px; top: 206px;
    font-size: 14.5px;
  }
  .card-front .band {
    position: absolute; left: 0; right: 0; bottom: 0; height: 44px;
    background: linear-gradient(var(--kelly-light), var(--kelly));
    display: flex; align-items: center; padding-left: 28px;
    font-size: 15px; letter-spacing: 2px; text-transform: uppercase;
  }

  /* Back card */
  .card-back {
    left: 630px;
    background: radial-gradient(ellipse at 55% 40%, var(--kelly-light) 0%, var(--kelly) 50%, var(--kelly-deep) 100%);
  }
  .card-back .lockup {
    position: absolute; left: 0; right: 0; top: 62px;
    display: flex; flex-direction: column; align-items: center;
  }
  .card-back .mark {
    width: 66px; height: 66px;
    background: var(--navy);
    border: 4px solid var(--white);
    margin-bottom: 16px;
  }
  .card-back .firm-tagline { color: var(--white); font-size: 14px; }
  .card-back .web {
    position: absolute; left: 26px; bottom: 20px;
    font-size: 13px; font-style: italic;
  }
</style>
</head>
<body>
<main class="canvas">
  <section class="card card-front" aria-label="Card front">
    <div class="mark" aria-hidden="true"></div>
    <div class="firm">
      <h1 class="firm-name">DORIAN KALVENFELD, P.A.</h1>
      <p class="firm-tagline">Personal Injury Attorneys</p>
    </div>
    <div class="person">
      <p class="person-name">Dorian Kalvenfeld</p>
      <p class="person-title">Attorney at Law</p>
    </div>
    <span class="divider" aria-hidden="true"></span>
    <ul class="contact">
      <li>Phone: 941.555.0147</li>
      <li>Fax: 941.555.0148</li>
      <li>Email: dorian@kalvenfeldlaw.com</li>
    </ul>
    <p class="address">2150 Harbor Crest Way Suite 210, Palm Hollow, Florida 34990</p>
    <div class="band">www.kalvenfeldlaw.com</div>
  </section>

  <section class="card card-back" aria-label="Card back">
    <div class="lockup">
      <div class="mark" aria-hidden="true"></div>
      <h2 class="firm-name">DORIAN KALVENFELD, P.A.</h2>
      <p class="firm-tagline">Personal Injury Attorneys</p>
    </div>
    <p class="web">www.kalvenfeldlaw.com</p>
  </section>
</main>
</body>
</html>
```